Book Cover for Lantern Cousins Notes from the Orchard

We have written a book that brings together Notes from the Orchard from a variety of women's voices.
We developed a draft book cover that we like using Canva (attached below). We'd love a book cover that is similar to this image, but looks more professional.
Following are the themes we’d like to depict in the book cover, and in parentheses, how they are represented in the current cover:
1. Divinely feminine (overall cover)
2. Currents of enlightenment (the swirls of light carrying the butterfly)
3. Diversity (a myriad of colors)
4. The solo journey into the unknown (the single butterfly’s flight)
5. Buoyancy and joy (again, the dancing colors and floating butterfly)
6. Boldly feminine (the blue butterfly, set against brush strokes of light)
7. Homage to a dear friend (she loved blue butterflies, the cosmos - this butterfly has hints of the cosmos in her wings, and painting - this background has brush strokes of light).
Book Title, Subtitle, and Editor:
Lantern Cousins
Notes from the Orchard
Edited by Ilse Varno
Thank you very much for considering this project!
People who are interested in Women and Spirituality

```html
<!DOCTYPE html>
<html lang="en">
<head>
<meta charset="utf-8">
<title>Lantern Cousins — Notes from the Orchard</title>
<link rel="stylesheet" href="https://fonts.googleapis.com/css2?family=Bodoni+Moda:opsz,wght@6..96,600&family=Great+Vibes&family=Archivo+Black&family=Libre+Baskerville&display=swap">
<style>
  :root {
    --backdrop: #cfcfcf;
    --cover: #ffffff;
    --cover-shade: #f1f1f1;
    --ink: #1f1f1f;
    --rule: #d9b8d6;
    --wing-red: #e8383d;
    --wing-orange: #f39a2b;
    --wing-yellow: #f4d935;
    --wing-green: #2aa77a;
    --wing-blue: #3b6fc4;
    --wing-violet: #7a3e9a;
  }
  * { margin: 0; padding: 0; box-sizing: border-box; }
  html, body {
    width: 1200px;
    height: 1200px;
    overflow: hidden;
    background: var(--backdrop);
  }
  .canvas {
    position: relative;
    width: 1200px;
    height: 1200px;
  }
  .book-cover {
    position: absolute;
    left: 230px;
    top: 45px;
    width: 740px;
    height: 1110px;
    background: linear-gradient(180deg, var(--cover) 0%, var(--cover) 60%, var(--cover-shade) 100%);
    box-shadow: 0 18px 40px rgba(0,0,0,0.18);
  }
  .title {
    position: absolute;
    left: 50px;
    top: 70px;
    width: 640px;
    height: 360px;
  }
  .title text {
    font-family: "Bodoni Moda", "Playfair Display", serif;
    font-weight: 600;
    font-size: 190px;
    fill: var(--ink);
  }
  .subtitle {
    position: absolute;
    left: 150px;
    top: 455px;
    width: 440px;
    text-align: center;
  }
  .subtitle-rule {
    height: 1px;
    background: var(--rule);
  }
  .subtitle-text {
    font-family: "Great Vibes", cursive;
    font-size: 50px;
    line-height: 1;
    color: var(--ink);
    padding: 16px 0 18px;
  }
  .butterfly-art {
    position: absolute;
    left: 190px;
    top: 600px;
    width: 360px;
    height: 360px;
  }
  .editor-credit {
    position: absolute;
    left: 0;
    right: 0;
    top: 1000px;
    text-align: center;
    font-family: "Libre Baskerville", serif;
    font-size: 30px;
    color: var(--ink);
  }
  .editor-name {
    font-family: "Archivo Black", sans-serif;
    font-size: 30px;
  }
</style>
</head>
<body>
<main class="canvas">
  <section class="book-cover">
    <svg class="title" viewBox="0 0 640 360" aria-label="Lantern Cousins">
      <text x="0" y="165" textLength="640" lengthAdjust="spacingAndGlyphs">LANTERN</text>
      <text x="0" y="345" textLength="640" lengthAdjust="spacingAndGlyphs">COUSINS</text>
    </svg>

    <div class="subtitle">
      <div class="subtitle-rule"></div>
      <p class="subtitle-text">Notes from the Orchard</p>
      <div class="subtitle-rule"></div>
    </div>

    <svg class="butterfly-art" viewBox="0 0 360 360" role="img" aria-label="Watercolour butterfly in rainbow colours, dissolving into a flight of small butterflies">
      <defs>
        <linearGradient id="wing-tones" x1="0" y1="1" x2="1" y2="0">
          <stop offset="0" stop-color="var(--wing-violet)"/>
          <stop offset="0.2" stop-color="var(--wing-blue)"/>
          <stop offset="0.4" stop-color="var(--wing-green)"/>
          <stop offset="0.6" stop-color="var(--wing-yellow)"/>
          <stop offset="0.8" stop-color="var(--wing-orange)"/>
          <stop offset="1" stop-color="var(--wing-red)"/>
        </linearGradient>
        <radialGradient id="art-fade" cx="0.5" cy="0.5" r="0.5">
          <stop offset="0.55" stop-color="#fff" stop-opacity="1"/>
          <stop offset="1" stop-color="#fff" stop-opacity="0"/>
        </radialGradient>
        <mask id="art-mask">
          <rect width="360" height="360" fill="url(#art-fade)"/>
        </mask>
      </defs>
      <rect width="360" height="360" fill="url(#wing-tones)" opacity="0.75" mask="url(#art-mask)"/>
    </svg>

    <p class="editor-credit">Edited by <span class="editor-name">Ilse Varno</span></p>
  </section>
</main>
</body>
</html>
```